Business Card for a Jewellery Brand

Business card for an upscale jewellery brand. Attached is the brand logo and icon and color board. I am looking for two card versions: one for the founder and one is generic. The card should be elegant and convey upscale and premium feel. I am open to both square and rectangle card shapes.

Industry/Entity Type

Jewelry

Contact Information for Business Card

Two cards: (1) Sunela Parvaniya (Founder) (2) General
(1) Sunela Parvaniya card should have Name: Sunela Parvaniya, Title: Founder Email id: sunela@quiremo.com.au. Phone no: +61452913307
(2) Generic card should have Email id: info@quiremo.com.au. Phone no: +61436207518

Requirements
Must have
• Workmark
• ICON
• Phone no
• Email ID
• ABN: 58219740312 (Note: ABN is Business number in Australia)
• Website: www.quiremo.com.au
• Instagram: quiremo_jewellery
• Facebook: @quiremojewellery
Nice to have
• Tagline

```html
<!DOCTYPE html>
<html lang="en">
<head>
<meta charset="utf-8">
<title>QUIREMO Business Cards</title>
<link href="https://fonts.googleapis.com/css2?family=Roboto:wght@300;400&display=swap" rel="stylesheet">
<style>
  :root {
    --backdrop: #55565a;
    --card: #ffffff;
    --blush: #dea6a1;
    --blush-tint: #f6e4e2;
    --panel: #e59a96;
    --band: #f8ad9f;
    --fold: #c4857f;
    --ink-light: #ffffff;
  }
  * { margin: 0; padding: 0; box-sizing: border-box; }
  html, body { width: 1200px; height: 1200px; overflow: hidden; }
  body {
    background: var(--backdrop);
    font-family: "Roboto", Arial, sans-serif;
    position: relative;
  }
  .card {
    position: absolute;
    left: 150px;
    width: 900px;
    height: 520px;
    background: var(--card);
    overflow: hidden;
  }
  .card--front { top: 60px; }
  .card--back { top: 620px; }

  .wordmark {
    position: absolute;
    color: var(--blush);
    font-weight: 400;
    letter-spacing: 0.3em;
    line-height: 1;
    white-space: nowrap;
  }
  .card--front .wordmark { left: 60px; top: 72px; font-size: 50px; }

  .accent-circle {
    position: absolute;
    border-radius: 50%;
    background: var(--blush-tint);
  }
  .card--front .accent-circle { left: 20px; top: 200px; width: 360px; height: 360px; }

  .contact-panel {
    position: absolute;
    left: 500px; top: 0;
    width: 400px; height: 520px;
    background: var(--panel);
  }
  .name-band {
    position: absolute;
    left: 460px; top: 48px;
    width: 440px; height: 96px;
    background: var(--band);
    padding: 18px 0 0 72px;
    color: var(--ink-light);
  }
  .name-band__fold {
    position: absolute;
    left: 460px; top: 144px;
    width: 0; height: 0;
    border-top: 40px solid var(--fold);
    border-left: 40px solid transparent;
  }
  .person-name { font-size: 30px; font-weight: 400; line-height: 1.1; }
  .person-title { font-size: 23px; font-weight: 300; opacity: 0.9; margin-top: 4px; }

  .address {
    position: absolute;
    left: 545px; top: 200px;
    color: var(--ink-light);
    font-size: 23px;
    font-style: normal;
    line-height: 1.3;
  }
  .contact-list {
    position: absolute;
    left: 548px; top: 296px;
    list-style: none;
    color: var(--ink-light);
    font-size: 23px;
  }
  .contact-list li {
    display: flex;
    align-items: center;
    gap: 8px;
    height: 34px;
  }
  .contact-list svg { width: 20px; height: 20px; flex: none; }
  .social-square {
    width: 18px; height: 18px; flex: none;
    background: var(--ink-light);
    margin: 0 1px;
  }

  .abn-band {
    position: absolute;
    left: 28px; top: 412px;
    width: 512px; height: 42px;
    background: var(--band);
    color: var(--ink-light);
    font-size: 22px;
    padding: 8px 0 0 62px;
  }
  .abn-band__fold {
    position: absolute;
    left: 500px; top: 454px;
    width: 0; height: 0;
    border-top: 24px solid var(--fold);
    border-right: 40px solid transparent;
  }

  .card--back .brand-lockup {
    position: absolute;
    left: 0; right: 0; top: 150px;
    display: flex;
    flex-direction: column;
    align-items: center;
    gap: 36px;
  }
  .card--back .accent-circle {
    position: static;
    width: 110px; height: 110px;
  }
  .card--back .wordmark {
    position: static;
    font-size: 60px;
    margin-left: 0.3em;
  }
</style>
</head>
<body>
  <section class="card card--front" aria-label="Founder business card, front">
    <div class="accent-circle"></div>
    <div class="wordmark">QUIREMO</div>

    <div class="contact-panel"></div>
    <div class="name-band">
      <div class="person-name">Sunela Parvaniya</div>
      <div class="person-title">Founder</div>
    </div>
    <div class="name-band__fold"></div>

    <address class="address">
      208 Larkmere Road, Suite 410<br>
      Halbury, Maryland 20914
    </address>

    <ul class="contact-list">
      <li>
        <svg viewBox="0 0 24 24" aria-hidden="true"><path fill="#fff" d="M6.6 10.8a15.1 15.1 0 0 0 6.6 6.6l2.2-2.2a1 1 0 0 1 1-.25 11.4 11.4 0 0 0 3.6.57 1 1 0 0 1 1 1V20a1 1 0 0 1-1 1A17 17 0 0 1 3 4a1 1 0 0 1 1-1h3.5a1 1 0 0 1 1 1c0 1.25.2 2.45.57 3.57a1 1 0 0 1-.25 1z"/></svg>
        +61452913307
      </li>
      <li>
        <svg viewBox="0 0 24 24" aria-hidden="true"><rect x="2" y="5" width="20" height="14" fill="#fff"/><path d="M2 5l10 8 10-8" fill="none" stroke="#e59a96" stroke-width="1.6"/></svg>
        sunela@quiremo.com.au
      </li>
      <li>
        <svg viewBox="0 0 24 24" aria-hidden="true" fill="none" stroke="#fff" stroke-width="1.8"><circle cx="12" cy="12" r="9"/><ellipse cx="12" cy="12" rx="4" ry="9"/><path d="M3 12h18"/></svg>
        www.quiremo.com.au
      </li>
      <li>
        <span class="social-square" aria-hidden="true"></span>
        quiremo_jewellery
      </li>
      <li>
        <span class="social-square" aria-hidden="true"></span>
        @quiremojewellery
      </li>
    </ul>

    <div class="abn-band">ABN: 58219740312</div>
    <div class="abn-band__fold"></div>
  </section>

  <section class="card card--back" aria-label="Business card, back">
    <div class="brand-lockup">
      <div class="accent-circle"></div>
      <div class="wordmark">QUIREMO</div>
    </div>
  </section>
</body>
</html>
```